Boutique Store Selling Antiques and Unique Finds

I need a Web Page designed for my Store Called "Willow Lane". I would like a very classic, muted design that looks European when pulled up. I will be selling Antiques from all over the world and Unique finds that have reproduced. I will also be selling high-end purses and jewelry with unique, reasonable products for the every-day buyer as well.

Target Market(s)

25-70 year old men and women;)

Coding

Coded - Design and coding required

Number of Pages Required

1 page

Colors

Designer to choose only greyscale colors for use in the design.

Requirements
Must have
• I want it

```html
<!DOCTYPE html>
<html lang="en">
<head>
<meta charset="UTF-8">
<title>Willow Lane — Antiques and Unique Finds</title>
<link rel="stylesheet" href="https://fonts.googleapis.com/css2?family=Noto+Serif:wght@400;700&family=Montserrat:wght@400;500&family=Roboto:wght@500&display=swap">
<style>
:root{
  --black:#000;
  --ink:#222;
  --white:#fff;
  --line:#d9d9d9;
  --price:#3b5a8a;
  --star:#b08a3a;
  --muted:#555;
  --serif:"Noto Serif", Georgia, serif;
}
*{box-sizing:border-box;margin:0;padding:0}
html,body{width:1200px;height:3255px;overflow:hidden;background:var(--white);font-family:var(--serif);color:var(--ink)}
.page{position:relative;width:1200px;height:3255px}
.abs{position:absolute}

.topbar{left:0;top:0;width:1200px;height:48px;background:var(--black);color:var(--white);font-size:15px}
.topbar .follows{position:absolute;left:86px;top:14px;display:flex;gap:12px;align-items:center}
.social-dot{display:inline-block;width:10px;height:10px;border-radius:50%;background:var(--white)}
.cart{position:absolute;left:1072px;top:10px}

.nav{left:0;top:48px;width:1200px;height:97px;background:var(--white)}
.nav a{position:absolute;top:42px;font-size:15px;color:var(--ink);text-decoration:none;letter-spacing:.3px}
.nav .home{left:86px;top:42px}
.nav .home::before{content:"";position:absolute;left:17px;top:-20px;width:12px;height:12px;border-radius:50%;background:var(--ink)}
.brand{position:absolute;left:483px;top:30px;width:200px;text-align:center;font-size:18px;letter-spacing:3px;font-variant:small-caps;color:var(--ink)}
.brand::before{content:"";display:block;margin:0 auto 6px;width:16px;height:16px;border-radius:50%;background:var(--ink)}
.signin{position:absolute;left:1017px;top:34px;width:94px;height:33px;background:var(--black);color:var(--white);font-weight:700;font-size:16px;display:flex;align-items:center;justify-content:center;box-shadow:0 2px 5px rgba(0,0,0,.3)}

.hero{left:0;top:145px;width:1200px;height:563px;background:linear-gradient(110deg,#8a7a6c 0%,#a49a8e 35%,#7b6f63 60%,#a38a82 85%,#6e5d55 100%)}
.hero h1{position:absolute;left:86px;top:160px;font-size:50px;font-weight:700;color:var(--white);letter-spacing:.5px}
.hero p{position:absolute;left:86px;top:246px;width:690px;font-size:15px;line-height:26px;color:var(--white)}
.hero .cta{position:absolute;left:86px;top:326px;width:153px;height:46px;background:var(--black);color:var(--white);font-weight:700;font-size:16px;display:flex;align-items:center;justify-content:center}
.arrow{position:absolute;top:262px}
.dots{position:absolute;left:571px;top:501px;display:flex;gap:8px}
.dots span{width:12px;height:12px;border-radius:50%;border:1.5px solid var(--white)}
.dots span.on{background:var(--white)}

.section-title{position:absolute;left:0;width:1200px;text-align:center;font-weight:700;font-size:40px;color:var(--black)}
.section-title::before{content:"";display:block;margin:0 auto 14px;width:22px;height:22px;border-radius:50%;background:var(--black)}

.product{position:absolute;top:938px;width:245px;height:388px;background:var(--white);box-shadow:0 1px 5px rgba(0,0,0,.15);text-align:center}
.product .photo{height:177px}
.product h3{margin-top:31px;font-size:15px;font-weight:400}
.price{font-family:"Montserrat",sans-serif;font-size:15px;color:var(--price)}
.product .price{margin-top:14px}
.stars{margin-top:12px;color:var(--star);font-size:16px;letter-spacing:4px}
.addcart{margin:14px auto 0;width:149px;height:42px;border:1px solid #999;border-radius:21px;font-family:"Roboto",sans-serif;font-weight:500;font-size:15px;color:#2d4a7a;display:flex;align-items:center;justify-content:center}

.find{position:absolute;width:499px;height:389px;border:1px solid var(--line);text-align:center;background:var(--white)}
.find .photo{height:299px}
.find h3{margin-top:22px;font-size:15px;font-weight:400}
.find .price{margin-top:4px}

.bestseller{left:0;top:2443px;width:600px;height:401px;background:var(--black);display:flex;align-items:center;justify-content:center}
.bestseller h2{color:var(--white);font-size:40px;font-weight:700;text-align:center}
.bestseller h2::before{content:"";display:block;margin:0 auto 14px;width:22px;height:22px;border-radius:50%;background:var(--white)}
.bestseller-photo{left:600px;top:2443px;width:600px;height:401px;background:radial-gradient(ellipse at 50% 55%,#6b5a3a 0%,#3c3222 45%,#b8ab96 80%)}

.footer{left:0;top:2844px;width:1200px;height:411px}
.f-brand{position:absolute;left:86px;top:52px;font-size:16px;letter-spacing:3px;font-variant:small-caps}
.f-brand::before{content:"";display:block;margin:0 0 5px 62px;width:14px;height:14px;border-radius:50%;background:var(--ink)}
.f-about{position:absolute;left:86px;top:130px;width:270px;font-size:15px;line-height:26px}
.f-col h4{font-size:17px;font-weight:400;margin-bottom:16px}
.f-col{position:absolute;top:48px}
.f-links li{list-style:none;font-size:14px;line-height:34px;color:#333}
.contact-row{display:flex;gap:14px;align-items:flex-start;font-size:15px;line-height:26px;margin-bottom:20px}
.ic{flex:none;width:28px;height:28px;border-radius:50%;background:var(--black);display:flex;align-items:center;justify-content:center}
.follow-row{display:flex;gap:16px;align-items:center;font-size:15px;margin-bottom:24px}
.follow-row i{width:9px;height:9px;border-radius:50%;background:var(--black)}
.f-rule{position:absolute;left:86px;top:334px;width:1028px;border-top:1px solid #444}
.copyright{position:absolute;left:0;top:366px;width:1200px;text-align:center;font-size:15px}
</style>
</head>
<body>
<div class="page">

  <header class="abs topbar">
    <div class="follows">Follows: <span class="social-dot"></span><span class="social-dot"></span><span class="social-dot"></span></div>
    <svg class="cart" width="44" height="30" viewBox="0 0 44 30" aria-label="Cart">
      <path d="M2 4h6l4 16h18l4-12H10" fill="none" stroke="#fff" stroke-width="2"/>
      <circle cx="14" cy="25" r="2.5" fill="#fff"/><circle cx="28" cy="25" r="2.5" fill="#fff"/>
      <circle cx="36" cy="6" r="5" fill="#fff"/><text x="36" y="9" font-size="8" text-anchor="middle" fill="#000" font-family="sans-serif">0</text>
    </svg>
  </header>

  <nav class="abs nav">
    <a class="home">HOME</a>
    <a style="left:188px">ABOUT US</a>
    <a style="left:322px">NEW ARRIVALS</a>
    <div class="brand">Willow Lane</div>
    <a style="left:733px">PRODUCT</a>
    <a style="left:863px">CONTACT US</a>
    <div class="signin">SIGN IN</div>
  </nav>

  <section class="abs hero" role="img" aria-label="Antique silver teapot, candelabra and trays on draped fabric">
    <h1>WILLOW LANE</h1>
    <p>Lorem ipsum dolor sit amet, consectetur adipiscing elit, sed do eiusmod<br>tempor incididunt ut labore et dolore magna aliqua. Ut enim ad minim veniam.</p>
    <div class="cta">GET STARTED</div>
    <svg class="arrow" style="left:40px" width="14" height="22"><path d="M11 3L3 11l8 8" fill="none" stroke="#fff" stroke-width="2.5"/></svg>
    <svg class="arrow" style="left:1145px" width="14" height="22"><path d="M3 3l8 8-8 8" fill="none" stroke="#fff" stroke-width="2.5"/></svg>
    <div class="dots"><span></span><span class="on"></span><span class="on"></span></div>
  </section>

  <h2 class="section-title" style="top:800px">OUR PRODUCT</h2>

  <article class="product" style="left:86px">
    <div class="photo" role="img" aria-label="Stone statue of a crowned king in a wood-panelled hall" style="background:linear-gradient(135deg,#5a3a26,#b7a990 55%,#4a2e1e)"></div>
    <h3>Lorem ipsum dolor</h3><div class="price">$ 20.00</div><div class="stars">★★★☆</div><div class="addcart">Add To Cart</div>
  </article>
  <article class="product" style="left:346px">
    <div class="photo" role="img" aria-label="Antique steel helmet resting on a stack of art books" style="background:linear-gradient(180deg,#e9e6e1,#5b5d5e 60%,#2c2e33)"></div>
    <h3>Lorem ipsum dolor</h3><div class="price">$ 20.00</div><div class="stars">★★★☆</div><div class="addcart">Add To Cart</div>
  </article>
  <article class="product" style="left:607px">
    <div class="photo" role="img" aria-label="Drawer of vintage spools, ribbons and sewing notions" style="background:linear-gradient(135deg,#9a8a5e,#4b463e 50%,#2d3340)"></div>
    <h3>Lorem ipsum dolor</h3><div class="price">$ 20.00</div><div class="stars">★★★☆</div><div class="addcart">Add To Cart</div>
  </article>
  <article class="product" style="left:868px">
    <div class="photo" role="img" aria-label="Wood-panelled stair hall with chandelier and statue" style="background:linear-gradient(135deg,#3d2618,#6e4a30 50%,#a89a86)"></div>
    <h3>Lorem ipsum dolor</h3><div class="price">$ 20.00</div><div class="stars">★★★☆</div><div class="addcart">Add To Cart</div>
  </article>

  <h2 class="section-title" style="top:1392px">ANTIQUES AND UNIQUE FINDS</h2>

  <article class="find" style="left:86px;top:1522px">
    <div class="photo" role="img" aria-label="Gilded star crown with blue stones on a stand" style="background:linear-gradient(180deg,#d8d2c6,#9c7f52 50%,#2d2d2d)"></div>
    <h3>Lorem ipsum dolor</h3><div class="price">$ 420.00</div>
  </article>
  <article class="find" style="left:611px;top:1522px">
    <div class="photo" role="img" aria-label="Brass star crown on an old leather book" style="background:linear-gradient(180deg,#c9c4b9,#8a6d3e 55%,#3a3226)"></div>
    <h3>Lorem ipsum dolor</h3><div class="price">$ 340.00</div>
  </article>
  <article class="find" style="left:86px;top:1969px">
    <div class="photo" role="img" aria-label="Velvet-lined gold crown resting on a stack of books" style="background:linear-gradient(180deg,#e3ded6,#2a2420 45%,#8a7252 80%)"></div>
    <h3>Lorem ipsum dolor</h3><div class="price">$ 420.00</div>
  </article>
  <article class="find" style="left:611px;top:1969px">
    <div class="photo" role="img" aria-label="Row of antique leather-bound books" style="background:linear-gradient(90deg,#4a3a2a,#7a5a3a 30%,#4a1e1a 55%,#1e1e1e 75%,#5a4a3a)"></div>
    <h3>Lorem ipsum dolor</h3><div class="price">$ 340.00</div>
  </article>

  <section class="abs bestseller"><h2>BEST SELLER</h2></section>
  <div class="abs bestseller-photo" role="img" aria-label="Ornate jewelled antique crown"></div>

  <footer class="abs footer">
    <div class="f-brand">Willow Lane</div>
    <p class="f-about">Sed ut perspiciatis unde omnis iste natus voluptatem accusantium doloremque laudantium, tot.</p>

    <div class="f-col" style="left:455px">
      <h4>Quicklinks</h4>
      <ul class="f-links"><li>Home</li><li>About Us</li><li>New Arrivals</li><li>Product</li><li>Blog</li><li>Contact Us</li></ul>
    </div>

    <div class="f-col" style="left:659px">
      <h4 style="margin-bottom:26px">Contact Us</h4>
      <div class="contact-row"><span class="ic"><svg width="14" height="14" viewBox="0 0 14 14"><path d="M3 1l2 3-1.5 1.5a8 8 0 0 0 5 5L10 9l3 2-1.5 2.5C6 13 1 8 .5 2.5z" fill="#fff"/></svg></span><span>123.456.7890</span></div>
      <div class="contact-row"><span class="ic"><svg width="14" height="10" viewBox="0 0 14 10"><rect x=".5" y=".5" width="13" height="9" fill="none" stroke="#fff"/><path d="M.5 .5L7 6l6.5-5.5" fill="none" stroke="#fff"/></svg></span><span>info@willowlane.com</span></div>
      <div class="contact-row"><span class="ic"><svg width="12" height="16" viewBox="0 0 12 16"><path d="M6 1a5 5 0 0 1 5 5c0 4-5 9-5 9S1 10 1 6a5 5 0 0 1 5-5z" fill="#fff"/><circle cx="6" cy="6" r="2" fill="#000"/></svg></span><span>34,Lorem ipsum dolor sit<br>ametconsectetur adipiscing</span></div>
    </div>

    <div class="f-col" style="left:1022px">
      <h4 style="margin-bottom:26px">Follows</h4>
      <div class="follow-row"><i></i>Lanebook</div>
      <div class="follow-row"><i></i>Chirper</div>
      <div class="follow-row"><i></i>linkwork</div>
    </div>

    <div class="f-rule"></div>
    <p class="copyright">©Copyright 2021 Willow Lane.All right reserved.</p>
  </footer>

</div>
</body>
</html>
```